Plainly Brisk Compostable Pet Waste Bags (60 count)

Our company (Plainly Brisk Pet Supplies) is developing a line of eco-friendly, compostable, dog waste bags (poop bags). The bags are GWR and VeroMulch certified. In addition to being fully compostable, we manufacture bags which are thicker, stronger, and more leak-proof than what is currently available on the market.

Target Market(s)

Middle to upper-class eco-concious pet owners.

Industry/Entity Type

Pet

Font styles to use
Sans Serif

Colors

Designer to choose colors to be used in the design.

Requirements
Must have
• On the front I need:
• The logo
• an indication of 60 bags
• The word "Compostable" needs to stand out
• The window will display the rolls of waste bags
• "Ultra thick" or something to that effect
• The back I need:
• The GWR Certificate -- the number is actually 73940216, if you can change that
• The VeroMulch logo -- the one that looks like a black and white ribbon with leaves coming out
• The UPC
• An indication of the bag being thicker than competitors (Typical bags are 18-20 microns thick, these are 24 microns thick)
• Generic "Ipsum lorem" text blurbs and headers (Please leave text editable -- I'll have my copywriter fill it in later on).
• Sides:
• Again, just general "Ipsum lorem" filler and headers, the copywriter will fill in at a later date.
Nice to have
• I'd like to avoid the natural (i.e. brown) cardboard look, as most of my competitors have gone that route. Colored kraft stock, or natural cardboard which is mostly printed (i.e. more ink than bare cardboard) is still good.

```html
<!DOCTYPE html>
<html lang="en">
<head>
<meta charset="utf-8">
<title>Plainly Brisk Compostable Pet Waste Bags – 60 count</title>
<link href="https://fonts.googleapis.com/css2?family=Patrick+Hand&family=Roboto+Slab:wght@300;400;700&display=swap" rel="stylesheet">
<style>
  :root{
    --page:#eeeeee;
    --lime:#9ad94a;
    --lime-light:#b8e86a;
    --grass:#6cc13a;
    --forest:#2f5d1e;
    --window:#3e6b2a;
    --window-band:#4a7a33;
    --sky:#7fe0f2;
    --sky-light:#b6f0fa;
    --cream:#fbf6c8;
    --badge-ring:#f2d93a;
    --white:#ffffff;
    --ink:#2b3a1c;
  }
  *{box-sizing:border-box;margin:0;padding:0}
  html,body{width:1200px;height:817px;overflow:hidden;background:var(--page)}
  .canvas{position:relative;width:1200px;height:817px;background:radial-gradient(circle at 50% 45%,#fbfbfb,var(--page) 80%)}

  .panel{position:absolute;overflow:hidden}

  /* top flap */
  .panel--top{left:460px;top:40px;width:440px;height:140px;
    background:linear-gradient(180deg,var(--lime-light),var(--lime));}
  .top__copy{position:absolute;left:30px;top:26px;width:250px;
    font:300 11px/1.45 "Roboto Slab",serif;color:var(--white);text-align:center}
  .top__tag{position:absolute;right:30px;top:24px;text-align:center;
    font:22px/1 "Patrick Hand",sans-serif;color:var(--white)}
  .top__icon{display:inline-block;border:2px solid var(--white);border-radius:14px;
    padding:3px 16px;font:400 12px/1 "Roboto Slab",serif;margin-bottom:8px}

  /* side panel */
  .panel--side{left:260px;top:180px;width:200px;height:560px;
    background:linear-gradient(180deg,var(--lime-light) 0%,var(--lime) 70%,var(--grass) 100%);}
  .side__badge{position:absolute;left:44px;top:22px}
  .side__thick{position:absolute;left:0;right:0;top:146px;text-align:center;
    font:28px/1 "Patrick Hand",sans-serif;color:var(--white)}
  .side__copy{position:absolute;left:22px;right:16px;top:190px;
    font:300 14px/1.35 "Roboto Slab",serif;color:var(--white)}
  .side__copy p+p{margin-top:16px}
  .side__email{position:absolute;left:22px;top:486px;
    font:700 12px/1 "Roboto Slab",serif;color:var(--forest)}
  .side__foot{position:absolute;left:0;right:0;bottom:0;height:110px;background:var(--white);
    border-top-left-radius:60% 40px;border-top-right-radius:60% 40px;
    display:flex;align-items:center;justify-content:center;gap:8px}

  /* front panel */
  .panel--front{left:460px;top:180px;width:440px;height:560px;background:var(--sky)}
  .front__scene{position:absolute;inset:0;
    background:linear-gradient(180deg,var(--sky) 0%,var(--sky-light) 38%,var(--grass) 52%,var(--lime) 72%,var(--cream) 100%)}
  .front__logo{position:absolute;left:18px;top:34px;display:flex;align-items:center;gap:8px;
    background:var(--white);border-radius:40px;padding:10px 18px}
  .front__thick{position:absolute;right:22px;top:48px;background:var(--white);border-radius:30px;
    padding:8px 16px;font:26px/1 "Patrick Hand",sans-serif;color:var(--grass)}
  .front__headline{position:absolute;left:0;right:0;top:132px;text-align:center;
    font:46px/1 "Patrick Hand",sans-serif;color:var(--white);letter-spacing:1px}
  .window{position:absolute;left:82px;top:196px;width:210px;height:290px;
    background:var(--window);border-radius:10px;overflow:hidden}
  .window__band{height:44px;background:var(--window-band);display:flex;align-items:center;justify-content:center;
    font:400 17px/1 "Roboto Slab",serif;letter-spacing:2px;color:var(--white)}
  .window__rolls{position:absolute;left:8px;right:8px;top:44px;bottom:8px;
    background:linear-gradient(180deg,#3f8a3c,#2e6d2c 48%,#3f8a3c 52%,#2a6327)}
  .front__badge{position:absolute;left:18px;top:420px}

  .logo__dot{width:30px;height:30px;border-radius:50%;background:var(--grass);flex:none}
  .logo__name{font:700 26px/1 "Roboto Slab",serif;color:var(--forest)}
  .side__foot .logo__name{font-size:20px}

  .badge__num{font:64px/0.9 "Patrick Hand",sans-serif;fill:var(--forest)}
  .badge__unit{font:20px/1 "Patrick Hand",sans-serif;fill:var(--grass)}
</style>
</head>
<body>
<main class="canvas">

  <section class="panel panel--top" aria-label="Top flap">
    <p class="top__copy">Lorem ipsum dolor sit amet, consectetuer adipiscing elit, sed diam nonummy nibh euismod tincidunt ut laoreet dolore magna aliquam erat volutpat. Ut wisi enim ad minim veniam, quis nostrud</p>
    <div class="top__tag"><span class="top__icon">ICON</span><br>LOREM<br>IPSUM</div>
  </section>

  <section class="panel panel--side" aria-label="Side panel">
    <svg class="side__badge" width="112" height="112" viewBox="0 0 112 112" aria-label="60 bags">
      <circle cx="56" cy="56" r="52" fill="var(--white)" stroke="var(--badge-ring)" stroke-width="4" stroke-dasharray="8 4"/>
      <text class="badge__num" x="56" y="68" text-anchor="middle">60</text>
      <text class="badge__unit" x="56" y="92" text-anchor="middle">BAGS</text>
    </svg>
    <h2 class="side__thick">ULTRA THICK</h2>
    <div class="side__copy">
      <p>Lorem ipsum dolor sit amet, adipiscing elit, sed diam nonummy nibh euismod tincidunt ut laoreet dolore magna aliquam erat volutpat.</p>
      <p>Lorem ipsum dolor sit amet, adipiscing elit, sed diam nonummy nibh euismod tincidunt laoreet dolore.</p>
    </div>
    <p class="side__email">all@plainlybrisk</p>
    <div class="side__foot">
      <span class="logo__dot"></span><span class="logo__name">Plainly Brisk</span>
    </div>
  </section>

  <section class="panel panel--front" aria-label="Front panel">
    <div class="front__scene" role="img" aria-label="Illustrated park scene with sky, clouds, trees, green hills, a path and a cartoon dog mascot"></div>
    <div class="front__logo"><span class="logo__dot"></span><span class="logo__name">Plainly Brisk</span></div>
    <p class="front__thick">ULTRA THICK</p>
    <h1 class="front__headline">LOREM IPSUM</h1>
    <div class="window">
      <div class="window__band">COMPOSTABLE</div>
      <div class="window__rolls" role="img" aria-label="Window showing green rolls of waste bags"></div>
    </div>
    <svg class="front__badge" width="112" height="112" viewBox="0 0 112 112" aria-label="60 bags">
      <circle cx="56" cy="56" r="52" fill="var(--white)" stroke="var(--badge-ring)" stroke-width="4" stroke-dasharray="8 4"/>
      <text class="badge__num" x="56" y="68" text-anchor="middle">60</text>
      <text class="badge__unit" x="56" y="92" text-anchor="middle">BAGS</text>
    </svg>
  </section>

</main>
</body>
</html>
```